Wine Label Logo NEW name too

We would like to see this done in more colors but, lighter ones too. the dark colors don't show up that well. Can you also do some on white wine and not just red wine?

Also, we aren't sure we will use the name Plumvale and wonder if you could use the name Honeyfrost with the same design to see how that looks, as well?

new wine label for a brand called Plumvale (one word) and is targeted to go after 21-40 year olds. Probably more women than men. There will be Plumvale Red, Plumvale White, Plumvale Cabernet, etc. the profile of the wine will be sweet...duh!!

would love you to come up with some TAG LINE ideas, as well. Size should be between 2 1/2 to 3 inches wide and 5 to 6 inches long. Needs place holders for varietal, Cabernet. 13.5% alcohol, area wil be California. I suggest you look at a bunch of wine labels to better understand this brief.

The final design should communicate fun, sweet, wine, young, hip

Wine labels matter. Period. Now, attempting to define “fun and contemporary” is nigh on impossible, but I think it would be safe to assume that this could mean “non-traditional.” Let’s face it. Design matters to millennial consumers. Quill, Tern Lodges, Loftly Journal – these brands are not ONLY for millennials by any means (well, maybe Tern), but design is top priority for these brands, and these brands have top priority for millennials. Feel free to do the math. If we spend money on something, we expect it to be beautiful and often times we expect social purchases like wine to act as a public reflection of our tastes and personality. This latter expectation is no different than any other generation (if arguably more intense due to our intrinsic personal branding tendencies); however, our personalities and what we are reflecting out to our peers IS different.
Updates

What about a label that is 2 1/2 to 3 inches wide and 5-6 inches long and looks like a white or off white piece of paper that has had berries poured across it with some stains and the name Plumvale Cabernet as the logo on the label?  Needs space for the AVA area grown to say California and the vintage 2011 and alcohol level in small letters 12.3%. 

Look at some wine labels to get a unique idea. Needs to appeal to 21-40 year old women. Needs to denote the wine is sweet

Reason: two partners are out of the country and I want them involved in the choice

Target Market(s)

Industry/Entity Type

Social

Logo Text

Plumvale Cabernet

Logo styles of interest
Pictorial/Combination Logo
Abstract Logo
Wordmark Logo

```html
<!DOCTYPE html>
<html lang="en">
<head>
<meta charset="utf-8">
<title>Plumvale Cabernet – Wine Label</title>
<link rel="stylesheet" href="https://fonts.googleapis.com/css2?family=Great+Vibes&family=Oswald:wght@500;600&family=Cormorant+Garamond:wght@500&family=Playfair+Display:ital,wght@1,900&display=swap">
<style>
  :root {
    --page: #f2f0ec;
    --slate: #6e8798;
    --slate-light: #8197a6;
    --slate-dark: #5b7384;
    --cream: #f1e7c9;
    --berry-red: #d3103d;
    --wine-red: #b81a42;
    --wine-muted: #9a7f8c;
    --glass-grey: #55535e;
  }
  * { margin: 0; padding: 0; box-sizing: border-box; }
  html, body {
    width: 1200px;
    height: 3600px;
    overflow: hidden;
    background: var(--page);
  }
  .canvas {
    position: relative;
    width: 1200px;
    height: 3600px;
  }
  .label {
    position: absolute;
    left: 100px;
    top: 860px;
    width: 1000px;
    height: 1880px;
    overflow: hidden;
    background:
      radial-gradient(ellipse at 30% 20%, var(--slate-light) 0%, transparent 60%),
      radial-gradient(ellipse at 80% 90%, var(--slate-dark) 0%, transparent 55%),
      var(--slate);
  }
  .illustration-area {
    position: absolute;
    left: 380px;
    top: 0;
    width: 620px;
    height: 1700px;
    background: linear-gradient(180deg,
      var(--wine-muted) 0%,
      var(--wine-red) 25%,
      var(--wine-red) 55%,
      var(--glass-grey) 100%);
    opacity: 0.85;
  }
  .brand-name {
    position: absolute;
    left: 60px;
    top: 1130px;
    font-family: "Great Vibes", cursive;
    font-weight: 400;
    font-size: 240px;
    line-height: 1;
    color: var(--cream);
    white-space: nowrap;
  }
  .varietal {
    position: absolute;
    left: 575px;
    top: 1385px;
    font-family: "Oswald", sans-serif;
    font-weight: 600;
    font-size: 48px;
    letter-spacing: 1px;
    line-height: 1;
    color: var(--berry-red);
  }
  .vintage {
    position: absolute;
    left: 500px;
    top: 1415px;
    font-family: "Cormorant Garamond", serif;
    font-weight: 500;
    font-size: 170px;
    line-height: 1;
    color: var(--cream);
  }
  .region {
    position: absolute;
    left: 170px;
    top: 1615px;
    font-family: "Playfair Display", serif;
    font-style: italic;
    font-weight: 900;
    font-size: 70px;
    line-height: 1;
    color: var(--berry-red);
  }
  .alcohol {
    position: absolute;
    left: 220px;
    top: 1705px;
    font-family: "Oswald", sans-serif;
    font-weight: 600;
    font-size: 44px;
    line-height: 1;
    color: var(--cream);
  }
</style>
</head>
<body>
  <main class="canvas">
    <section class="label">
      <div class="illustration-area" role="img" aria-label="Illustration of a wine glass filled with red wine, with a single red berry and leaf hanging from a thin string beside it"></div>
      <h1 class="brand-name">Plumvale</h1>
      <p class="varietal">CABERNET</p>
      <p class="vintage">2012</p>
      <p class="region">California</p>
      <p class="alcohol">13,5%</p>
    </section>
  </main>
</body>
</html>
```